Professional violinist needs business cards

I am trying to attract the following jobs:
-private violin lessons (primarily classical)
-performance gigs (weddings, birthday parties, funerals, etc.)
-collaborations with other artists (studio recordings, performances)

I want to communicate that I have a very high standard of excellence for my work, but I also love people and celebrations.
Values/style words I like are:
love, joy, peace, fun, beauty, authenticity, excellence, warmth, refined/sleek, free spirited. If that's too confusing, just ignore :)

I will attach my favorite business card template that I could find on Canva. The lines are supposed to be like a music staff, which I think is really cool, but I also don't want it to look too busy. I like the simple black and white--I think it looks sharp--but I also am open to other ideas. I also have seen business cards with pictures included that looked great, so I attached an image that could be used as well.

I am also attaching a file that I made of my initials that could be used as a logo, but I'm not sure if it should be included.

Information on the card:
-My name (18 letters total)
-"violinist"
-phone number, email, website

Thank you!

```html
<!DOCTYPE html>
<html lang="en">
<head>
<meta charset="UTF-8">
<title>Elena Marwood · Violinist · Business Cards</title>
<link rel="stylesheet" href="https://fonts.googleapis.com/css2?family=Raleway:wght@400;500;600&family=Arimo:wght@400&display=swap">
<style>
  :root {
    --page-bg: #2b2b2b;
    --card-black: #050505;
    --card-charcoal: #1c1c1c;
    --gold: #d19f3a;
    --gold-deep: #b9862b;
    --white: #f2f2f2;
    --photo-dark: #141010;
    --photo-warm: #5a3a28;
  }
  * { box-sizing: border-box; margin: 0; padding: 0; }
  html, body {
    width: 1200px; height: 900px; overflow: hidden;
    background: var(--page-bg);
  }
  .canvas {
    position: relative; width: 1200px; height: 900px;
  }
  .card {
    position: absolute; left: 240px; width: 720px; height: 411px;
    overflow: hidden;
    box-shadow: 0 10px 30px rgba(0,0,0,0.55);
  }

  /* Front */
  .card--front { top: 24px; background: var(--card-black); }
  .staff { position: absolute; inset: 0; width: 100%; height: 100%; }
  .staff line { stroke: var(--gold); stroke-width: 4; }
  .front-name {
    position: absolute; left: 40px; top: 160px;
    font-family: "Raleway", sans-serif; font-weight: 500;
    font-size: 62px; line-height: 80px; color: var(--gold);
    background: var(--card-black); padding: 0 16px;
    letter-spacing: 1px;
  }
  .front-web {
    position: absolute; right: 34px; bottom: 78px;
    font-family: "Arimo", sans-serif; font-size: 15px;
    color: var(--white); letter-spacing: 1px;
    background: var(--card-black); padding: 0 6px;
  }

  /* Back */
  .card--back {
    top: 465px;
    background: linear-gradient(90deg, var(--card-black) 0%, var(--card-black) 50%, var(--card-charcoal) 100%);
  }
  .gold-band {
    position: absolute; left: 0; top: 30px; bottom: 0; width: 96px;
    background: linear-gradient(180deg, var(--gold) 0%, var(--gold-deep) 100%);
  }
  .portrait {
    position: absolute; left: 60px; top: 0; width: 240px; height: 411px;
    background: radial-gradient(ellipse at 45% 40%, var(--photo-warm) 0%, var(--photo-dark) 70%);
  }
  .identity {
    position: absolute; left: 330px; top: 88px;
  }
  .identity__name {
    font-family: "Raleway", sans-serif; font-weight: 500;
    font-size: 30px; color: var(--gold); letter-spacing: 0.5px;
  }
  .identity__role {
    font-family: "Raleway", sans-serif; font-weight: 400;
    font-size: 15px; color: var(--white); margin-top: 2px;
  }
  .contacts {
    position: absolute; right: 30px; bottom: 44px;
    list-style: none;
    font-family: "Arimo", sans-serif; font-size: 17px; color: var(--white);
  }
  .contacts li {
    display: flex; justify-content: flex-end; align-items: center;
    gap: 14px; height: 26px;
  }
  .contacts svg { width: 16px; height: 16px; fill: var(--gold); flex: none; }
</style>
</head>
<body>
<main class="canvas">

  <section class="card card--front" aria-label="Card front">
    <svg class="staff" viewBox="0 0 720 411" preserveAspectRatio="none" aria-hidden="true">
      <line x1="0" y1="40"  x2="720" y2="40"/>
      <line x1="0" y1="120" x2="720" y2="120"/>
      <line x1="0" y1="200" x2="720" y2="200"/>
      <line x1="0" y1="280" x2="720" y2="280"/>
      <line x1="0" y1="360" x2="720" y2="360"/>
    </svg>
    <p class="front-name">Elena Marwood</p>
    <p class="front-web">www.yourwebsite.com</p>
  </section>

  <section class="card card--back" aria-label="Card back">
    <div class="gold-band"></div>
    <div class="portrait" role="img" aria-label="Photo of the violinist in a black dress holding her violin and bow"></div>
    <div class="identity">
      <h1 class="identity__name">Elena Marwood</h1>
      <p class="identity__role">Violinist</p>
    </div>
    <ul class="contacts">
      <li>012 3456 7890
        <svg viewBox="0 0 16 16" aria-hidden="true"><path d="M1 6c0-2 3-3 7-3s7 1 7 3v1h-3.5V5.5h-7V7H1z"/><path d="M3 8h10l1 6H2z"/></svg>
      </li>
      <li>info@yourwebsite.com
        <svg viewBox="0 0 16 16" aria-hidden="true"><path d="M1 3h14v10H1z M2.5 4.5 8 9l5.5-4.5v-.2h-11z" fill-rule="evenodd"/></svg>
      </li>
      <li>www.yourwebsite.com
        <svg viewBox="0 0 16 16" aria-hidden="true"><path d="M8 1a7 7 0 1 0 0 14A7 7 0 0 0 8 1zm0 1.5a5.5 5.5 0 1 1 0 11 5.5 5.5 0 0 1 0-11zM3 7.3h10v1.4H3zM7.3 2.5h1.4v11H7.3z"/></svg>
      </li>
    </ul>
  </section>

</main>
</body>
</html>
```